Looking for someone to design a business card for my plumbing business Quandor Plumbing Solutions I want the background also to be black, must attract clients. If possible I want the front to be the logo and the back to show maybe the details.

Target Market(s)

Clients

Industry/Entity Type

Plumbing maintenance

Contact Information for Business Card

Name: Felix, Contact: 0461 539 207, Email: quandorplumbingsolutions@mailbrook.example, Licence number 728093K

Font styles to use
Other font styles liked:
• as per logo maybe?

Colors

Designer to choose colors to be used in the design.

Requirements
Nice to have
• stating the service I provide, emergency plumbing, plumbing maintenance, drainage maintenance, block sewer and stormwater, camera and locating.

```html
<!DOCTYPE html>
<html lang="en">
<head>
<meta charset="utf-8">
<title>Quandor Plumbing Solutions – Business Card</title>
<link href="https://fonts.googleapis.com/css2?family=Figtree:wght@400;700;800&display=swap" rel="stylesheet">
<style>
  :root {
    --stage: #141415;
    --card: #1f1f20;
    --blue: #4a90d2;
    --white: #f2f2f2;
    --soft: #e6e6e6;
    --ghost: #2e2e30;
  }
  * { margin: 0; padding: 0; box-sizing: border-box; }
  html, body { width: 1200px; height: 1059px; overflow: hidden; background: var(--stage); }
  body { position: relative; font-family: "Figtree", sans-serif; color: var(--white); }

  .card {
    position: absolute;
    width: 690px;
    height: 392px;
    background: var(--card);
    border-radius: 20px;
    overflow: hidden;
  }
  .card--front { left: 257px; top: 89px; }
  .card--back  { left: 254px; top: 547px; }

  .brand {
    position: absolute;
    left: 0; right: 0;
    display: flex;
    align-items: center;
    justify-content: center;
    gap: 12px;
    font-weight: 800;
    text-transform: uppercase;
    letter-spacing: 0.5px;
    white-space: nowrap;
  }
  .brand__dot { width: 22px; height: 22px; border-radius: 50%; background: var(--blue); flex: none; }
  .card--front .brand { top: 106px; font-size: 28px; color: var(--white); }
  .card--back .brand { top: 150px; font-size: 32px; color: var(--ghost); }

  .person {
    position: absolute;
    right: 450px;
    top: 255px;
    text-align right;
    text-align: right;
    white-space: nowrap;
  }
  .person__name { font-size: 26px; font-weight: 700; color: var(--blue); line-height: 34px; letter-spacing: 0.5px; }
  .person__role { font-size: 15px; line-height: 20px; color: var(--soft); }
  .person__licence { font-size: 15px; line-height: 20px; color: var(--soft); margin-top: 6px; }

  .divider { position: absolute; left: 257px; top: 262px; width: 2px; height: 66px; background: var(--blue); }

  .contact { position: absolute; left: 276px; top: 255px; list-style: none; }
  .contact li { display: flex; align-items: center; height: 26px; font-size: 15px; color: var(--soft); white-space: nowrap; }
  .contact svg { width: 13px; height: 13px; margin-right: 8px; flex: none; }

  .services {
    position: absolute;
    left: 0; right: 0;
    top: 310px;
    text-align: center;
    font-size: 15px;
    line-height: 27px;
    color: var(--soft);
    white-space: nowrap;
  }
  .services .sep { color: var(--blue); margin: 0 8px; font-size: 18px; }
</style>
</head>
<body>
  <section class="card card--front" aria-label="Card front">
    <div class="brand"><span class="brand__dot"></span>Quandor Plumbing Solutions</div>

    <div class="person">
      <p class="person__name">FELIX</p>
      <p class="person__role">Founder &amp; CEO</p>
      <p class="person__licence">Licence number 728093K</p>
    </div>

    <div class="divider"></div>

    <ul class="contact">
      <li>
        <svg viewBox="0 0 24 24" aria-hidden="true"><path fill="#4a90d2" d="M6.6 10.8a15 15 0 0 0 6.6 6.6l2.2-2.2a1 1 0 0 1 1-.25 11.4 11.4 0 0 0 3.6.57 1 1 0 0 1 1 1V20a1 1 0 0 1-1 1A17 17 0 0 1 3 4a1 1 0 0 1 1-1h3.5a1 1 0 0 1 1 1c0 1.25.2 2.45.57 3.57a1 1 0 0 1-.25 1z"/></svg>
        0461 539 207
      </li>
      <li>
        <svg viewBox="0 0 24 24" aria-hidden="true"><rect x="2" y="5" width="20" height="14" rx="1" fill="#4a90d2"/><path d="M2.5 5.5 12 13l9.5-7.5" fill="none" stroke="#1f1f20" stroke-width="1.6"/></svg>
        quandorplumbingsolutions@mailbrook.example
      </li>
      <li>
        <svg viewBox="0 0 24 24" aria-hidden="true"><circle cx="12" cy="12" r="11" fill="#4a90d2"/></svg>
        @QuandorPlumbingSolutions
      </li>
    </ul>
  </section>

  <section class="card card--back" aria-label="Card back">
    <div class="brand"><span class="brand__dot"></span>Quandor Plumbing Solutions</div>

    <div class="services">
      <p>Emergency plumbing<span class="sep">•</span>Plumbing maintenance<span class="sep">•</span>Drainage maintenance</p>
      <p>Block sewer and stormwater<span class="sep">•</span>Camera and locating</p>
    </div>
  </section>
</body>
</html>
```